Yoga/movement guide/teacher for adult yoga practice and kid yoga

What is the positioning or mission statement of your company? to guide individuals in a yoga-based safe and sustainable movement practice applicable to all ages and body types. Currently my focus is working with children in daycare and school settings, but my goal is to expand into private yoga practice for adults, and potentially as part of rented space in studios. I hope to find a way to work with children AND adults (so would love for logo to be appealing to both), but current focus is with children based on need and demand in the community. yoga for children also compliments my backround as a pediatrician/neonatologist, and I greatly miss interacting with children. I also want to emphasize a yoga/movement practice that is focused more on what one feels internally through movement. NOT what one looks like asthetically. I believe in removing all mirrors from yoga/movement practice. It should be an experience of movement/poses/yoga through appropriate cueing and education. It is not about the details of how far the knee should bend, or how high the leg should be. Focusing on foudation first, core, then core engagement and ultimately expression of poses/movements. A focus on strength, stability and mobility, not just flexibility, which is the common perception/association with yoga. I also want individuals to learn to be an advocate of their own health. Through guidance, I hope for individuals to connect with their body so they know themselves so well to be able to advocate for themselves in the modern healthcare world. This internal experience and connection is so essential in a world where modern medicine has become a business and it is all about making a dollar. the connection with patients is lost, and individuals need to learn to empower themselves and through their new found voice to be able to articulate what is wrong.<br/>Does your company have a tagline or slogan that should be included with the logo? "Move With Inner Light"<br/>What do you hope your company can be known for? Accessible yoga for a sustained practice. A guided movement practice where one gains information and knowledge of oneself through a mind/body connection. For one feel good physically with a new awaraness of their internal radiance that exists in all beings. Physical rejuvenation egnites a light and increases energy to flow through the physical body, which ultimately tranlates into works of kindness for others and out in the world. <br/>What color palettes might you prefer? why? love the colors currently chosen<br/>Where will the logo be primarily used? initially business cards, but hopefully future websites, t-shirts, and potentially local magazine adds. Also starting with a small couple of banners for community events in the area. I currently practice as a nomad out of my car :)<br/>Are there any elements you would prefer to see in the logo? Movement. A modern depiction of a human body/figure practicing movement. Hoping to avoid a stereotypical yoga pose per say, just because I want to people to think of it more of a movement practice with yoga roots. Modern yoga. There are elements of breathing and connecting with oneself through the flow of breath and movement, but I do not focus on the meditative/cerebral aspect of the yoga practice. What I teach is almost reaching a meditative state through movement. I personally don't practice, nor resonate with just seated meditation. just not my thing :)<br/>In your opinion, what defines a well-designed logo? curiosity. enough info for individuals to think they know what it means, but want to know more. invokes curiosity, but not too abstract. Reproducible. not too complicated. I want also to invoke a community feel, so a design that appeals to all people within a community. <br/>What is your preference in reference to icons, typography, spokespeople (characters), etc.? modern design. I love the idea of a logo for my purposes, to invoke a sense of movement from within. So not too static. <br/>What words or icons must be included in the logo? movement with yoga roots. <br/>What logos do you like and why? A representation, but not exact. I think some ambiguity is intriguing for others, and also memorable. I want it to be an artistic representation of movement/yoga<br/>What logos do you dislike and why? too busy, too loud. <br/>In your opinion, what is the primary purpose for a logo? association<br/>Who is the primary target audience? (who is most likely to use your services/product?) Children and their parents, but ultimately to expand into teaching adults. I even have aspirations of prenatal and post-natal yoga. Potentially incorporating infants. <br/>Who currently uses your product the most? n/a (working in schools/daycare currently. It is currently all volunteer)<br/>Are you pleased with the range of people your company serves? n/a<br/>Are you looking to expand, modify, or completely change your target audience? or will it remain the same? yes! expand into an adult audience. <br/>How do you plan to focus on your target audience? currently by working through schools and daycares. hopefully ultimately through after school care programs and then offering kid yoga in an existing yoga studio (working on this with Q Studio in Ridgeland, currently)<br/>What are your main forms of advertising? word of mouth, schools, daycares. Happy kids talking to their parents about the yoga class they took and happy teachers :)<br/>How do most customers find out about your company?<br/>Which gender are you targeting? All genders! However, with kid yoga, often the maternal individual in the child's life is more involved with decision making as far as extracurricular activities

Target Market(s)

individuals and families interested in wellness and feeling great

Contact Information for Business Card

Dana Whitford
Yoga Instructor
RYT-200, RCYT

certified yoga teacher for adults and children

Colors

Designer to choose colors to be used in the design.

Requirements
Must have
• "Move With Inner Light"
Nice to have
• logo with same colors

```html
<!DOCTYPE html>
<html lang="en">
<head>
<meta charset="utf-8">
<title>Glowfield Studios – Business Card</title>
<link rel="stylesheet" href="https://fonts.googleapis.com/css2?family=Lato:wght@400;700&display=swap">
<style>
  :root{
    --bg:#2a2a2a;
    --card-white:#ffffff;
    --card-grey:#7a7a7a;
    --pattern-grey:#737373;
    --sun:#f5d93a;
    --teal:#5ec8cf;
    --icon-teal:#29b3a5;
    --icon-grey:#8a8a8a;
    --ink:#4a4a4a;
    --rule:#9a9a9a;
  }
  *{box-sizing:border-box;margin:0;padding:0}
  html,body{width:1200px;height:1108px;overflow:hidden}
  body{background:var(--bg);font-family:"Lato",Arial,sans-serif;position:relative}
  .card{position:absolute;top:224px;width:380px;height:660px;border-radius:22px;box-shadow:0 10px 28px rgba(0,0,0,.45)}
  .card--front{left:170px;background:var(--card-white);text-align:center;color:var(--ink)}
  .card--back{left:650px;background:var(--card-grey);overflow:hidden}

  .brand{position:absolute;top:150px;left:0;right:0;display:flex;align-items:center;justify-content:center;gap:14px}
  .brand__dot{width:46px;height:46px;border-radius:50%;background:var(--sun)}
  .brand__name{font-size:34px;font-weight:400;color:var(--ink);letter-spacing:.5px}
  .tagline{position:absolute;top:212px;left:0;right:0;font-size:13px;letter-spacing:3px;text-transform:uppercase;color:var(--teal)}

  .person{position:absolute;top:330px;left:0;right:0}
  .person__name{font-size:27px;font-weight:700;line-height:1.1}
  .person__first{color:var(--teal)}
  .person__last{color:var(--sun)}
  .person__role{font-size:19px;margin-top:4px}

  .divider{position:absolute;top:414px;left:70px;right:70px;display:flex;align-items:center;gap:6px}
  .divider__line{flex:1;height:1px;background:var(--rule)}
  .contact-icon{width:24px;height:24px;border-radius:50%;display:flex;align-items:center;justify-content:center}
  .contact-icon--phone{background:var(--sun)}
  .contact-icon--mail{background:var(--icon-teal)}
  .contact-icon--web{background:var(--icon-grey)}

  .contacts{position:absolute;top:448px;left:0;right:0;font-size:19px;line-height:29px}
  .rule{position:absolute;top:546px;left:90px;right:90px;height:1px;background:var(--rule)}
  .address{position:absolute;top:560px;left:0;right:0;font-size:19px;line-height:27px}

  .back-pattern{position:absolute;inset:0;background:radial-gradient(circle at 50% 50%,var(--card-grey),var(--pattern-grey))}
  .back-brand{position:absolute;top:470px;left:0;right:0;display:flex;align-items:center;justify-content:center;gap:8px}
  .back-brand__dot{width:18px;height:18px;border-radius:50%;background:var(--sun)}
  .back-brand__name{font-size:15px;color:var(--card-white)}
  .social{position:absolute;top:566px;left:0;right:0;display:flex;justify-content:center;gap:8px}
  .social__ring{width:30px;height:30px;border-radius:50%;border:1.5px solid var(--sun)}
</style>
</head>
<body>
  <section class="card card--front">
    <div class="brand">
      <span class="brand__dot"></span>
      <span class="brand__name">Glowfield Studios</span>
    </div>
    <p class="tagline">Move With Inner Light</p>

    <div class="person">
      <p class="person__name"><span class="person__first">Owen</span> <span class="person__last">Hartley</span></p>
      <p class="person__role">Managing Director</p>
    </div>

    <div class="divider">
      <span class="divider__line"></span>
      <span class="contact-icon contact-icon--phone">
        <svg width="13" height="13" viewBox="0 0 24 24"><path fill="#fff" d="M6.6 10.8a15 15 0 0 0 6.6 6.6l2.2-2.2c.3-.3.7-.4 1-.2 1.1.4 2.3.6 3.6.6.6 0 1 .4 1 1V20c0 .6-.4 1-1 1A17 17 0 0 1 3 4c0-.6.4-1 1-1h3.5c.6 0 1 .4 1 1 0 1.3.2 2.5.6 3.6.1.3 0 .7-.2 1z"/></svg>
      </span>
      <span class="contact-icon contact-icon--mail">
        <svg width="13" height="13" viewBox="0 0 24 24"><rect x="3" y="6" width="18" height="12" rx="1" fill="none" stroke="#fff" stroke-width="2"/><path d="M3 7l9 6 9-6" fill="none" stroke="#fff" stroke-width="2"/></svg>
      </span>
      <span class="contact-icon contact-icon--web">
        <svg width="13" height="13" viewBox="0 0 24 24"><circle cx="12" cy="12" r="9" fill="none" stroke="#fff" stroke-width="2"/><path d="M3 12h18M12 3c3 3 3 15 0 18M12 3c-3 3-3 15 0 18" fill="none" stroke="#fff" stroke-width="1.6"/></svg>
      </span>
      <span class="divider__line"></span>
    </div>

    <div class="contacts">
      <p>044-987 654 321</p>
      <p>hello@glowfield.com</p>
      <p>www.glowfieldstudios.com</p>
    </div>
    <div class="rule"></div>
    <div class="address">
      <p>88 Linden Row,</p>
      <p>20315, Brookvale</p>
    </div>
  </section>

  <section class="card card--back">
    <div class="back-pattern" role="img" aria-label="Faint repeating pattern of the studio emblem on grey"></div>
    <div class="back-brand">
      <span class="back-brand__dot"></span>
      <span class="back-brand__name">Glowfield Studios</span>
    </div>
    <div class="social">
      <span class="social__ring"></span>
      <span class="social__ring"></span>
      <span class="social__ring"></span>
      <span class="social__ring"></span>
    </div>
  </section>
</body>
</html>
```